New Website for World Wide Charity (KOLVAN)

We need a dynamic web design for our brand new charity organisation that will be working worldwide. We will be funded by donations so need to attract people to donate.

What We Do
We work to optimise the wellbeing of the planet, the animals and all that live within. Our slogan is Achieving Vibrational Equilibrium.

We have included a Powerpoint document which may help you understand what we need, it is just an idea for structure and style, it is not set in stone so feel free to be as creative as you like!
Updates

Designs look the same

Target Market(s)

Adults 18+ with an interest in animal, environmental. Businesses that may like to support our natural world or already support our natural world.

Number of Pages Required

3 page

Colors

Designer to choose colors to be used in the design.

Requirements
Must have
• We need the website to be easy to use and understand.

Web pages will be Home, What We Do, Who We Are, Success Stories, What You Can Do (Blog section), Seek Help, Donate, Join.
Nice to have
• Natural feel, easy to navigate, Ideally the website will look natural and organic.

Natural colours, blues, greens, sand, gold, brown, grey, silver, Orange and yellow for impact.
Should not have
• Should not have a dark coloured theme.

```html
<!DOCTYPE html>
<html lang="en">
<head>
<meta charset="utf-8">
<title>KOLVAN – Help Raise World Vibration</title>
<link rel="stylesheet" href="https://fonts.googleapis.com/css2?family=Arimo:wght@400;700&display=swap">
<style>
:root{
  --blue:#26528f;
  --blue-deep:#10357a;
  --blue-band:#1d3f72;
  --green-deep:#04301a;
  --forest:#4d6b55;
  --orange:#f08a12;
  --orange-bright:#ff8100;
  --gold:#ffd21a;
  --white:#ffffff;
  --text:#3b3b3b;
}
*{margin:0;padding:0;box-sizing:border-box}
html,body{width:1200px;height:2782px;overflow:hidden}
body{font-family:'Arimo',Arial,sans-serif;background:var(--white);color:var(--text);position:relative}
.abs{position:absolute}

.hero-bg{left:0;top:0;width:1200px;height:750px;background:linear-gradient(180deg,var(--blue) 0%,var(--blue) 60%,#4b6fa7 80%,#ffffff 100%)}
.hero-forest{left:607px;top:-40px;width:900px;height:820px;border-radius:50%;overflow:hidden;
  background:linear-gradient(200deg,#8c8a4c 0%,#4a6a53 30%,#3a5d55 60%,rgba(75,110,160,.4) 85%,rgba(255,255,255,0) 100%)}
.logo-wave{left:0;top:0}
.logo-mark{left:150px;top:7px;width:104px;height:104px;border-radius:50%;border:2px solid var(--blue);background:#fff;
  display:flex;align-items:center;justify-content:center;font-size:14px;font-weight:700;color:var(--blue)}
.nav{left:325px;top:47px;display:flex;gap:0;font-size:14px;color:#fff}
.nav a{color:#fff;text-decoration:none;position:absolute;white-space:nowrap}
.nav a.active{color:var(--gold)}

.hero-title{left:148px;top:193px;font-size:30px;font-weight:700;color:#fff;letter-spacing:.2px}
.hero-copy{left:150px;top:243px;width:480px;font-size:14.6px;line-height:22.6px;color:#fff}
.btn{display:flex;align-items:center;justify-content:center;background:var(--blue-deep);color:#fff;font-size:14px;text-transform:uppercase}
.hero-btn{left:150px;top:355px;width:210px;height:41px}

.cards{left:150px;top:472px;width:900px;height:300px;display:flex}
.card{width:300px;height:300px;position:relative;display:flex;align-items:center;justify-content:center;color:#fff;font-size:22px;font-weight:700;letter-spacing:1px}
.card-env{background:linear-gradient(160deg,#14512a 0%,var(--green-deep) 60%)}
.card-animal{background:linear-gradient(160deg,#f39a22,#ef8412);flex-direction:column}
.card-human{background:linear-gradient(160deg,#3c5f98,#2d5190)}
.card-frame{position:absolute;left:31px;top:32px;width:238px;height:238px;border:2px solid #fff}
.card-animal h3{position:absolute;top:72px;width:100%;text-align:center;font-size:22px}
.card-animal p{position:absolute;top:118px;left:45px;width:210px;text-align:center;font-size:12.6px;line-height:18px;font-weight:400;letter-spacing:0}
.card-animal .btn{position:absolute;left:69px;top:197px;width:162px;height:29px;background:var(--blue);font-size:12.5px;font-weight:400;letter-spacing:0}

.mist{left:0;top:1231px;width:1200px;height:840px;background:linear-gradient(180deg,#ffffff 0%,#8aa0c7 10%,#5f7eb0 25%,#4d6fa6 55%,#7d95bf 80%,#ffffff 100%)}

.blob-back,.blob{position:absolute;border-radius:58% 42% 52% 48% / 48% 56% 44% 52%}
.section-title{position:absolute;font-size:26px;font-weight:700;color:var(--blue);letter-spacing:.8px}
.section-copy{position:absolute;width:400px;font-size:14.6px;line-height:22.5px;color:var(--text)}
.section-copy p+p{margin-top:22.5px}
.light{color:#fff}

.footer{left:0;top:2458px;width:1200px;height:324px;background:var(--blue)}
.footer-bar{left:0;top:2751px;width:1200px;height:31px;background:var(--blue-band)}
.footer-logo{left:191px;top:2511px;width:86px;height:86px;border-radius:50%;background:#fff;border:2px solid #9fb1d4;
  display:flex;align-items:center;justify-content:center;font-size:12px;font-weight:700;color:var(--blue)}
.footer-about{left:156px;top:2603px;width:200px;font-size:14px;line-height:22.6px;color:#fff}
.footer-col{position:absolute;top:2520px;color:#fff;font-size:14px;text-transform:uppercase}
.footer-col h4{font-size:14px;font-weight:700;margin-bottom:34px}
.footer-col li{list-style:none;height:30px;font-weight:700}
.copyright{left:156px;top:2759px;font-size:14px;color:#fff}
.social{left:895px;top:2759px;display:flex;gap:13px}
.social span{width:16px;height:16px;border-radius:50%;background:#fff;display:block}
</style>
</head>
<body>

<div class="abs hero-bg"></div>
<div class="abs hero-forest" role="img" aria-label="Misty pine forest at sunset"></div>

<svg class="abs logo-wave" width="310" height="170" viewBox="0 0 310 170">
  <path d="M0 150 C40 130 80 115 140 112 C200 110 290 130 300 70 L300 0 L0 0 Z" fill="var(--blue-deep)"/>
  <path d="M0 142 C40 122 80 108 140 104 C200 100 280 118 292 60 L292 0 L0 0 Z" fill="#ffffff"/>
</svg>
<div class="abs logo-mark">KOLVAN</div>

<nav class="abs nav">
  <a class="active" style="left:0">Home</a>
  <a style="left:79px">What We Do</a>
  <a style="left:200px">Who We Are</a>
  <a style="left:321px">Success Stories</a>
  <a style="left:463px">What You Can Do</a>
  <a style="left:618px">Donate and Join.</a>
</nav>

<h1 class="abs hero-title">HELP RAISE WORLD VIBRATION</h1>
<p class="abs hero-copy">Lorem ipsum dolor sit amet, consectetur adipiscing elit. Aenean ante eros, ullamcorper quis dignissim eget, volutpat interdum lectus. Sed interdum convallis dui et lobortis. Sed lobortis ex venenatis magna congue aliquam. Vivamus</p>
<div class="abs btn hero-btn">Make a difference</div>

<div class="abs cards">
  <div class="card card-env" role="img" aria-label="Small topiary tree in a pot">ENVIRONMENT</div>
  <div class="card card-animal" role="img" aria-label="Two puppies in a flower field">
    <div class="card-frame"></div>
    <h3>ANIMAL</h3>
    <p>tincidunt nulla nec malesuada accumsan. Fusce acinia, sapien ac suscipit ultricies, libero urna</p>
    <div class="btn">FIND OUT MORE</div>
  </div>
  <div class="card card-human" role="img" aria-label="Elderly man sitting with head bowed">HUMAN</div>
</div>

<div class="abs mist" role="img" aria-label="Misty mountains reflected in a lake"></div>

<!-- Environment -->
<div class="blob-back" style="left:175px;top:821px;width:422px;height:455px;background:var(--green-deep)"></div>
<div class="blob" role="img" aria-label="Close-up of a leafy topiary tree" style="left:151px;top:828px;width:425px;height:452px;background:radial-gradient(circle at 45% 40%,#3f7a35 0%,#1f4522 40%,#16261a 75%)"></div>
<h2 class="section-title" style="left:650px;top:828px">ENVIRONMENT</h2>
<div class="section-copy" style="left:652px;top:870px">
  <p>mattis sapien, at iaculis ligula massa sit amet mauris. Sed a tincidunt arcu. Praesent massa dolor, finibus non cursus dapibus, ultrices a nisl. Cras maximus bibendum eros, non rutrum arcu bibendum nec. Etiam quis orci leo. Class aptent taciti sociosqu ad litora torquent per conubia nostra, per inceptos himenaeos. Pellentesque aliquet scelerisque risus sit amet lobortis.</p>
  <p>In lobortis, tortor et elementum laoreet, mi nibh gravida tortor, ac dapibus lacus augue at felis. Pellentesque pharetra in diam et sodales. Mauris nec velit eu velit mattis elementum ac in dui. Proin sit amet elit non nulla sodales faucibus. Donec ultricies vel justo nec accumsan. Nulla sollicitudin efficitur tempor. Lorem ipsum dolor sit amet, consectetur adipiscing elit. Curabitur egestas vehicula est, at molestie lectus condimentum non. Donec leo justo, eleifend sed nisl nec, scelerisque ultrices felis. Interdum et</p>
</div>

<!-- Animal -->
<h2 class="section-title light" style="left:149px;top:1440px">ANIMAL</h2>
<div class="section-copy light" style="left:149px;top:1486px">
  <p>mattis sapien, at iaculis ligula massa sit amet mauris. Sed a tincidunt arcu. Praesent massa dolor, finibus non cursus dapibus, ultrices a nisl. Cras maximus bibendum eros, non rutrum arcu bibendum nec. Etiam quis orci leo. Class aptent taciti sociosqu ad litora torquent per conubia nostra, per inceptos himenaeos. Pellentesque aliquet scelerisque risus sit amet lobortis.</p>
  <p>In lobortis, tortor et elementum laoreet, mi nibh gravida tortor, ac dapibus lacus augue at felis. Pellentesque pharetra in diam et sodales. Mauris nec velit eu velit mattis elementum ac in dui. Proin sit amet elit non nulla sodales faucibus. Donec ultricies vel justo nec accumsan. Nulla sollicitudin efficitur tempor. Lorem ipsum dolor sit amet, malesuada fames ac ante ipsum primis in faucibus.</p>
</div>
<div class="blob-back" style="left:610px;top:1391px;width:430px;height:456px;background:var(--orange-bright)"></div>
<div class="blob" role="img" aria-label="Two golden retriever puppies sitting in grass and orange flowers" style="left:624px;top:1398px;width:429px;height:449px;background:linear-gradient(180deg,#8fa86a 0%,#c9a36d 45%,#d7b07a 65%,#6f8a3c 85%,#e07a2a 100%)"></div>

<!-- Human -->
<div class="blob-back" style="left:175px;top:1962px;width:436px;height:446px;background:var(--blue)"></div>
<div class="blob" role="img" aria-label="Elderly man in a cap and green jacket sitting bowed" style="left:151px;top:1970px;width:445px;height:438px;background:linear-gradient(150deg,#d8c7a8 0%,#9aa36e 35%,#6c7a45 65%,#2f3320 100%)"></div>
<h2 class="section-title" style="left:650px;top:2009px">HUMAN</h2>
<div class="section-copy" style="left:653px;top:2053px">
  <p>mattis sapien, at iaculis ligula massa sit amet mauris. Sed a tincidunt arcu. Praesent massa dolor, finibus non cursus dapibus, ultrices a nisl. Cras maximus bibendum eros, non rutrum arcu bibendum nec. Etiam quis orci leo. Class aptent taciti sociosqu ad litora torquent per conubia nostra, per inceptos himenaeos. Pellentesque aliquet scelerisque risus sit amet lobortis.</p>
  <p>In lobortis, tortor et elementum laoreet, mi nibh gravida tortor, ac dapibus lacus augue at felis. Pellentesque pharetra in diam et sodales. Mauris nec velit eu velit mattis elementum ac in dui. Proin sit amet elit non nulla sodales faucibus. Donec ultricies vel justo nec accumsan. Nulla sollicitudin efficitur tempor. Lorem ipsum dolor sit amet,</p>
</div>

<!-- Footer -->
<footer>
  <div class="abs footer"></div>
  <div class="abs footer-bar"></div>
  <div class="abs footer-logo">KOLVAN</div>
  <p class="abs footer-about">Suspendisse ut suscipit tortor. Sed in risus turpis. Suspendisse cursus porta felis, sed aliquet ex ullamcorper id. Aliquam fringilla dolor vitae metus hendrerit, sollicitudin</p>
  <div class="footer-col" style="left:437px">
    <h4>Get involved</h4>
    <ul><li>Join us</li><li>Fundraise</li><li>Donate</li><li>Shop</li></ul>
  </div>
  <div class="footer-col" style="left:641px">
    <h4>Get help</h4>
    <ul><li>Contact us</li><li>Media</li></ul>
  </div>
  <div class="footer-col" style="left:826px">
    <h4>Legal</h4>
    <ul><li>Terms and conditions</li><li>Cookies</li><li>Privacy policy</li></ul>
  </div>
  <p class="abs copyright">© All Rights are Reserved</p>
  <div class="abs social" aria-label="Social links"><span></span><span></span><span></span><span></span></div>
</footer>

</body>
</html>
```